Business Card Design Project

Doctor, Pain Management. Need a new business card design with appointment info on the back. New address is 18 Corvell Road, Suite 304, Brisdale, NJ 07391. Right now I believe the rest of the information is staying the same.

```html
<!DOCTYPE html>
<html lang="en">
<head>
<meta charset="utf-8">
<title>Brisdale Pain Care – Business Card</title>
<link href="https://fonts.googleapis.com/css2?family=Cinzel:wght@500&family=Roboto:wght@400;500;700&family=Open+Sans:ital,wght@0,400;1,400&family=Tenor+Sans&display=swap" rel="stylesheet">
<style>
  :root{
    --bg:#e9e6e1;
    --card-dark:#1a1b1d;
    --band-dark:#23221a;
    --yellow:#f6f53c;
    --accent-yellow:#e8e33a;
    --sky:#6fc6ea;
    --ink:#1b1b1b;
    --paper:#ffffff;
    --rule:#6b6b6b;
  }
  *{box-sizing:border-box;margin:0;padding:0}
  html,body{width:1200px;height:911px;overflow:hidden;background:var(--bg)}
  .stage{position:relative;width:1200px;height:911px}

  /* Front card */
  .card-front{position:absolute;left:140px;top:150px;width:340px;height:580px;background:var(--card-dark);border-radius:4px;overflow:hidden;box-shadow:0 6px 18px rgba(0,0,0,.25)}
  .front-panel{position:absolute;left:0;top:0;width:340px;height:330px}
  .contact{position:absolute;left:40px;top:48px;width:270px;text-align:center;font-family:"Roboto",sans-serif;color:var(--ink);font-size:15px;line-height:1.45}
  .contact .gap{height:14px}
  .contact .web{font-weight:700}
  .front-brand{position:absolute;left:0;top:370px;width:340px;text-align:center;font-family:"Tenor Sans",sans-serif;color:var(--accent-yellow);font-size:22px;display:flex;justify-content:center;align-items:center;gap:10px}
  .brand-dot{width:14px;height:14px;border-radius:50%;background:var(--sky)}
  .doctor{position:absolute;left:0;top:470px;width:340px;text-align:center}
  .doctor-name{font-family:"Cinzel",serif;color:var(--sky);font-size:21px;letter-spacing:.5px}
  .doctor-title{font-family:"Roboto",sans-serif;font-weight:500;color:var(--accent-yellow);font-size:15px;margin-top:4px}

  /* Back card */
  .card-back{position:absolute;left:540px;top:300px;width:600px;height:350px;background:var(--paper);border-radius:4px;overflow:hidden;box-shadow:0 6px 18px rgba(0,0,0,.25)}
  .back-band{height:120px;background:var(--band-dark);display:flex;align-items:center;justify-content:center;gap:14px}
  .back-brand{font-family:"Tenor Sans",sans-serif;color:var(--accent-yellow);font-size:30px}
  .form{padding:26px 36px 0;font-family:"Open Sans",sans-serif;color:var(--ink);font-size:15px}
  .field{display:flex;align-items:flex-end;gap:8px;margin-bottom:16px}
  .field .line{flex:1;border-bottom:1px dotted var(--rule);height:14px}
  .field .suffix{font-size:11px}
  .row{display:flex;gap:20px}
  .row .field{flex:1}
  .days{display:flex;justify-content:space-between;margin:4px 0 16px}
  .day{display:flex;align-items:center;gap:6px}
  .box{width:13px;height:13px;border:1px solid var(--ink)}
  .notice{font-style:italic;font-size:12px;text-align:center;line-height:1.5}
</style>
</head>
<body>
<div class="stage">

  <section class="card-front">
    <svg class="front-panel" viewBox="0 0 340 330" aria-hidden="true">
      <path d="M22 18 H300 V255 Q230 255 200 300 Q180 318 170 330 Q160 318 140 300 Q110 255 22 255 Z" fill="var(--yellow)"/>
    </svg>
    <div class="contact">
      <p>18 Corvell Road, Suite 304</p>
      <p>Brisdale, NJ 07391</p>
      <div class="gap"></div>
      <p>P. 732.555.0148</p>
      <p>F. 732.555.0149</p>
      <p>brisdalepain.desk@gmail.com</p>
      <div class="gap"></div>
      <p class="web">www.brisdalepaincare.com</p>
    </div>
    <div class="front-brand"><span class="brand-dot"></span>Brisdale Pain Care</div>
    <div class="doctor">
      <p class="doctor-name">MEILIN ZHOU, M.D., PH.D.</p>
      <p class="doctor-title">Board Certified Anesthiologist</p>
    </div>
  </section>

  <section class="card-back">
    <div class="back-band">
      <span class="brand-dot"></span>
      <span class="back-brand">Brisdale Pain Care</span>
    </div>
    <div class="form">
      <div class="field"><span>Name :</span><span class="line"></span></div>
      <div class="row">
        <div class="field"><span>Date:</span><span class="line"></span></div>
        <div class="field"><span>Time :</span><span class="line"></span><span class="suffix">AM/PM</span></div>
      </div>
      <div class="days">
        <span class="day">Sun <span class="box"></span></span>
        <span class="day">Mon <span class="box"></span></span>
        <span class="day">Tue <span class="box"></span></span>
        <span class="day">Wed <span class="box"></span></span>
        <span class="day">Thu <span class="box"></span></span>
        <span class="day">Fri <span class="box"></span></span>
        <span class="day">Sat <span class="box"></span></span>
      </div>
      <p class="notice">Please give me 24 hours notice if you are unable to keep your appointment or<br>a cancellation fee may be charged.</p>
    </div>
  </section>

</div>
</body>
</html>
```